BildeVOLD buisnesscard

Hey :) I need a modern buisnesscard for my company BildeVOLD
It most have:
Dagligleder og Fotograf: Henrik Audun Strandvik

Mob: +4791264085
Epost: post@bildevold.example
Adresse: Kvernbakken9, 6040 Strandholm

Facbook and instagram logo with text BildeVOLD

BildeVOLD logo

It Company

```html
<!DOCTYPE html>
<html lang="no">
<head>
<meta charset="utf-8">
<title>BildeVOLD – visittkort</title>
<link rel="stylesheet" href="https://fonts.googleapis.com/css2?family=Open+Sans:wght@400;600;700&display=swap">
<style>
  :root {
    --backdrop: #4a4a4a;
    --paper: #ffffff;
    --brand-blue: #2580b3;
    --brand-pink: #c94a8a;
    --ink-light: #ffffff;
    --font-main: "Open Sans", Arial, sans-serif;
  }
  * { box-sizing: border-box; margin: 0; padding: 0; }
  html, body {
    width: 1105px; height: 1200px; overflow: hidden;
    background: var(--backdrop);
    font-family: var(--font-main);
  }
  .card {
    position: absolute; left: 193px; width: 720px; height: 410px;
  }
  .card--front { top: 167px; background: var(--paper); }
  .card--back { top: 623px; background: var(--brand-blue); }

  .brand {
    position: absolute; left: 0; right: 0; top: 150px;
    display: flex; justify-content: center; align-items: center; gap: 14px;
  }
  .brand__dot {
    width: 24px; height: 24px; border-radius: 50%; background: var(--brand-pink);
  }
  .brand__name {
    font-size: 50px; font-weight: 700; color: var(--brand-blue); letter-spacing: -0.5px;
    line-height: 1.2;
  }

  .info-band {
    position: absolute; left: 0; right: 0; top: 272px; height: 116px;
    display: flex; gap: 4px;
  }
  .info-band__person {
    width: 364px; background: var(--brand-blue); color: var(--ink-light);
    padding: 14px 0 0 39px;
  }
  .person__name { font-size: 25px; font-weight: 600; line-height: 1.2; }
  .person__role, .person__address { font-size: 19px; line-height: 1.4; }
  .person__address { margin-left: 4px; }

  .info-band__contact {
    flex: 1; background: var(--brand-pink); color: var(--ink-light);
    padding: 16px 22px 0 0; text-align: right;
  }
  .contact__row {
    display: flex; justify-content: flex-end; align-items: center; gap: 8px;
    font-size: 18px; line-height: 1.5;
  }
  .contact__row svg { width: 18px; height: 18px; flex: none; }

  .back__name {
    position: absolute; left: 0; right: 0; top: 130px; text-align: center;
    font-size: 92px; font-weight: 700; color: var(--ink-light); letter-spacing: -1px;
  }
  .social {
    position: absolute; left: 0; right: 0; top: 336px;
    display: flex; justify-content: center; align-items: center; gap: 6px;
  }
  .social__line {
    width: 126px; height: 2px;
    background: linear-gradient(90deg, rgba(255,255,255,0), #ffffff);
  }
  .social__line--right { background: linear-gradient(90deg, #ffffff, rgba(255,255,255,0)); width: 110px; }
  .social__dot {
    width: 37px; height: 37px; border-radius: 50%; border: 2px solid var(--ink-light);
  }
</style>
</head>
<body>
  <section class="card card--front">
    <div class="brand">
      <span class="brand__dot"></span>
      <span class="brand__name">BildeVOLD</span>
    </div>
    <div class="info-band">
      <div class="info-band__person">
        <p class="person__name">Henrik Audun Strandvik</p>
        <p class="person__role">Dagligleder og Fotograf</p>
        <p class="person__address">Kvernbakken9, 6040 Strandholm</p>
      </div>
      <div class="info-band__contact">
        <p class="contact__row">+4791264085
          <svg viewBox="0 0 18 18" aria-hidden="true"><rect x="4.5" y="1" width="9" height="16" rx="1.5" fill="none" stroke="#fff" stroke-width="1.8"/><rect x="7.5" y="14" width="3" height="1.4" fill="#fff"/></svg>
        </p>
        <p class="contact__row">post@bildevold.example
          <svg viewBox="0 0 18 18" aria-hidden="true"><rect x="1" y="4" width="16" height="11" fill="#fff"/><path d="M1 4 L9 10 L17 4" fill="none" stroke="#c94a8a" stroke-width="1.4"/></svg>
        </p>
        <p class="contact__row">www.bildevold.example
          <svg viewBox="0 0 18 18" aria-hidden="true"><circle cx="9" cy="9" r="8" fill="#fff"/><ellipse cx="9" cy="9" rx="3.5" ry="8" fill="none" stroke="#c94a8a" stroke-width="1.2"/><line x1="1" y1="9" x2="17" y2="9" stroke="#c94a8a" stroke-width="1.2"/></svg>
        </p>
      </div>
    </div>
  </section>

  <section class="card card--back">
    <p class="back__name">BildeVOLD</p>
    <div class="social">
      <span class="social__line"></span>
      <span class="social__dot" role="img" aria-label="Sosial profil 1 for BildeVOLD"></span>
      <span class="social__dot" role="img" aria-label="Sosial profil 2 for BildeVOLD"></span>
      <span class="social__line social__line--right"></span>
    </div>
  </section>
</body>
</html>
```